Business Card Design

Business Card for professional consulting firm working with large financial institutions.

Target Market(s)

Executive buyers

Industry/Entity Type

Banking

Contact Information for Business Card

Mild creativity wanted. Not boring, but do elaborate artwork.

Font styles to use
Serif
Sans Serif

Colors

Designer to choose colors to be used in the design.

Requirements
Must have
• Standard business card features - company name, individual name, telephone, website, email, locations.
Nice to have
• Two colors
Should not have
• too many colors, fancy printing, cartoons.

```html
<!DOCTYPE html>
<html lang="en">
<head>
<meta charset="utf-8">
<title>northvale – Business Card</title>
<link href="https://fonts.googleapis.com/css2?family=Oswald:wght@500&family=Work+Sans:wght@400&display=swap" rel="stylesheet">
<style>
  :root {
    --backdrop: #262626;
    --card: #1c1c1c;
    --card-edge: #2a2a2a;
    --ink-light: #f2f2f2;
    --ink-silver: #c9c9c9;
    --ink-muted: #b5b5b5;
  }
  * { margin: 0; padding: 0; box-sizing: border-box; }
  html, body {
    width: 1200px;
    height: 900px;
    overflow: hidden;
    background: var(--backdrop);
  }
  .canvas {
    width: 1200px;
    height: 900px;
    display: flex;
    flex-direction: column;
    align-items: center;
    justify-content: center;
    gap: 40px;
  }
  .card {
    position: relative;
    width: 700px;
    height: 400px;
    background: linear-gradient(135deg, var(--card) 0%, var(--card-edge) 100%);
    box-shadow: 0 10px 30px rgba(0,0,0,0.45);
  }
  .card-front {
    display: flex;
    align-items: center;
    justify-content: center;
  }
  .brand {
    display: flex;
    align-items: center;
    gap: 14px;
    font-family: "Work Sans", sans-serif;
    font-weight: 400;
    font-size: 52px;
    color: var(--ink-light);
    letter-spacing: 1px;
  }
  .brand-dot {
    width: 16px;
    height: 16px;
    border-radius: 50%;
    background: var(--ink-silver);
  }
  .identity {
    position: absolute;
    left: 150px;
    top: 150px;
    width: 230px;
    text-align: right;
  }
  .person-name {
    font-family: "Oswald", sans-serif;
    font-weight: 500;
    font-size: 38px;
    line-height: 1;
    color: var(--ink-silver);
    letter-spacing: 0.5px;
    text-transform: uppercase;
  }
  .person-role {
    font-family: "Work Sans", sans-serif;
    font-size: 17px;
    color: var(--ink-muted);
    margin-top: 4px;
    letter-spacing: 0.5px;
  }
  .divider {
    position: absolute;
    left: 408px;
    top: 150px;
    width: 2px;
    height: 66px;
    background: var(--ink-silver);
  }
  .contact-list {
    position: absolute;
    left: 432px;
    top: 148px;
    list-style: none;
    font-family: "Work Sans", sans-serif;
    font-size: 18px;
    color: var(--ink-light);
    line-height: 24px;
  }
  .contact-list li {
    display: flex;
    align-items: center;
    gap: 10px;
  }
  .contact-list svg {
    width: 12px;
    height: 12px;
    flex: none;
  }
  .address {
    position: absolute;
    left: 220px;
    top: 322px;
    font-family: "Work Sans", sans-serif;
    font-size: 18px;
    color: var(--ink-light);
    letter-spacing: 0.5px;
  }
</style>
</head>
<body>
  <main class="canvas">
    <section class="card card-front">
      <div class="brand"><span class="brand-dot"></span>northvale</div>
    </section>

    <section class="card card-back">
      <div class="identity">
        <h1 class="person-name">Daniel Harper</h1>
        <p class="person-role">Director</p>
      </div>
      <div class="divider"></div>
      <ul class="contact-list">
        <li>
          <svg viewBox="0 0 12 12"><path d="M2.5 1 L4.5 1 L5.2 3.6 L4 4.5 Q5 6.8 7.5 8 L8.4 6.8 L11 7.5 L11 9.5 Q10.6 11 9 11 Q3.5 10.3 1 3 Q1 1.4 2.5 1 Z" fill="#b5b5b5"/></svg>
          +330 1875-4412
        </li>
        <li>
          <svg viewBox="0 0 12 12"><rect x="1" y="2.5" width="10" height="7" fill="none" stroke="#b5b5b5" stroke-width="1.2"/><path d="M1 2.5 L6 6.5 L11 2.5" fill="none" stroke="#b5b5b5" stroke-width="1.2"/></svg>
          info@northvale.com
        </li>
        <li>
          <svg viewBox="0 0 12 12"><circle cx="6" cy="6" r="5" fill="none" stroke="#b5b5b5" stroke-width="1.1"/><ellipse cx="6" cy="6" rx="2.2" ry="5" fill="none" stroke="#b5b5b5" stroke-width="1"/><line x1="1" y1="6" x2="11" y2="6" stroke="#b5b5b5" stroke-width="1"/></svg>
          www.northvale.com
        </li>
      </ul>
      <p class="address">48 Elmwood Rd, Bramford VIC 3712</p>
    </section>
  </main>
</body>
</html>
```